van singage

My wife started a home cleaning company in Oct last year
We recently purchased a white corrant almeda lwb crew cab van
We need advertising on the van but it will also be used for school run Shopping and days out etc.
So the design would have to reflect a high quality cleaning company
But also with a young fresh twist awesome
don't just want a mobile advert i would like a cool looking van
don't want a full wrap because of the cost, but may consider a half wrap
We have some images of logos and a business cards that I will upload
Sparkle by Tamsin. SbT.
Updates

half wrap ie - backend and lower part of van

Industry/Entity Type

Advertising

Font styles to use
Decorative
Script

Colors

Designer to choose colors to be used in the design.

Requirements
Must have
• Needs to include website, logo and phone number

```html
<!DOCTYPE html>
<html lang="en">
<head>
<meta charset="utf-8">
<title>Sparkle by Tamsin – Van Rear Signage</title>
<link rel="stylesheet" href="https://fonts.googleapis.com/css2?family=Great+Vibes&family=Questrial&display=swap">
<style>
  :root {
    --van-white: #f7f7f5;
    --backdrop: #e6e6e3;
    --brand-red: #c8141b;
    --brand-red-deep: #9e0c12;
    --band-black: #0d0d0d;
    --ink: #2a2a2a;
    --white: #ffffff;
    --swirl-tint: rgba(255, 255, 255, 0.2);
    --monogram-tint: rgba(120, 6, 10, 0.35);
  }
  * { margin: 0; padding: 0; box-sizing: border-box; }
  html, body {
    width: 1200px;
    height: 1002px;
    overflow: hidden;
    background: var(--backdrop);
  }
  .signage {
    position: relative;
    width: 1200px;
    height: 1002px;
    background: var(--van-white);
  }
  .window-graphic {
    position: absolute;
    left: 60px;
    top: 170px;
    width: 1080px;
    height: 440px;
  }
  .window-graphic svg {
    position: absolute;
    inset: 0;
    width: 100%;
    height: 100%;
  }
  .monogram-area {
    position: absolute;
    left: 20px;
    top: 10px;
    width: 420px;
    height: 300px;
    background: radial-gradient(ellipse closest-side, var(--monogram-tint), transparent);
  }
  .flourish-area {
    position: absolute;
    right: 0;
    top: 0;
    width: 340px;
    height: 260px;
    background: radial-gradient(ellipse closest-side at 65% 40%, var(--swirl-tint), transparent);
  }
  .brand-name {
    position: absolute;
    left: 430px;
    top: 60px;
    font-family: "Great Vibes", cursive;
    font-weight: 400;
    color: var(--white);
    line-height: 0.9;
  }
  .brand-name .line-one {
    display: block;
    font-size: 118px;
  }
  .brand-name .line-two {
    display: block;
    font-size: 104px;
    padding-left: 40px;
  }
  .brand-rule {
    position: absolute;
    left: 410px;
    top: 282px;
    width: 560px;
    height: 3px;
    background: var(--white);
  }
  .tagline {
    position: absolute;
    left: 0;
    top: 344px;
    width: 1080px;
    text-align: center;
    font-family: "Questrial", sans-serif;
    font-size: 48px;
    color: var(--white);
    letter-spacing: 0.5px;
  }
  .contact {
    position: absolute;
    left: 596px;
    top: 690px;
    font-family: "Questrial", sans-serif;
    font-size: 42px;
    color: var(--ink);
    list-style: none;
  }
  .contact li {
    display: flex;
    align-items: center;
    height: 62px;
  }
  .contact li::before {
    content: "";
    display: inline-block;
    width: 4px;
    height: 42px;
    margin-right: 18px;
    background: var(--brand-red);
  }
</style>
</head>
<body>
  <main class="signage">
    <section class="window-graphic">
      <svg viewBox="0 0 1080 440" preserveAspectRatio="none" aria-hidden="true">
        <defs>
          <linearGradient id="red-panel" x1="0" y1="0" x2="1" y2="1">
            <stop offset="0" stop-color="#c8141b"/>
            <stop offset="1" stop-color="#9e0c12"/>
          </linearGradient>
        </defs>
        <path d="M22,0 H1058 Q1080,0 1080,22 V350 H0 V22 Q0,0 22,0 Z" fill="url(#red-panel)"/>
        <path d="M0,330 C320,296 720,300 1080,318 V425 C720,445 320,430 0,410 Z" fill="#0d0d0d"/>
      </svg>
      <div class="monogram-area" role="img" aria-label="Faint large script monogram decoration"></div>
      <div class="flourish-area" role="img" aria-label="Soft white swirl ornament"></div>
      <h1 class="brand-name">
        <span class="line-one">Sparkle</span>
        <span class="line-two">by Tamsin</span>
      </h1>
      <div class="brand-rule"></div>
      <p class="tagline">For All of Your Cleaning Needs</p>
    </section>
    <ul class="contact">
      <li class="contact-phone">07700 900418</li>
      <li class="contact-web">SparkleByTamsin.com</li>
    </ul>
  </main>
</body>
</html>
```